Ferncrest Roam Wording For Logo & Business card

I have the logo, I just need the "Ferncrest Roam" wording to go with it, and a business card design. The only thing on the business card is the website info. We provide nature connection experiences, and bolster these efforts through writing and host a platform for community around it.

I also have an idea of what it could look like (sketch), though I'm really not sure how it would come out. I am open to the best design and happy to consider original artwork. You can see what the site is about at FerncrestRoam.example.

Contact Information for Business Card

The only thing on the business card is the website info and the design. I will put other messaging on the back.

Website lettering (FerncrestRoam.example) in Montserrat

Logo Text

Ferncrest Roam (letters optional)

Font styles to use
Other font styles liked:
• montserrat

```html
<!DOCTYPE html>
<html lang="en">
<head>
<meta charset="utf-8">
<title>Ferncrest Roam – Business Card</title>
<link href="https://fonts.googleapis.com/css2?family=Montserrat:wght@500;700&display=swap" rel="stylesheet">
<style>
  :root {
    --backdrop: #e9e9e7;
    --card-white: #f7f7f6;
    --ink-navy: #1c1733;
    --accent-red: #d42f12;
    --flame-yellow: #f7c200;
    --flame-orange: #e8650a;
    --flame-deep: #c23a06;
    --logo-plum: #2a1640;
    --reverse-white: #f4f1ee;
  }
  * { margin: 0; padding: 0; box-sizing: border-box; }
  html, body { width: 1200px; height: 801px; overflow: hidden; }
  body {
    background: var(--backdrop);
    display: flex;
    align-items: center;
    justify-content: center;
    gap: 48px;
    font-family: "Montserrat", Arial, sans-serif;
  }
  .card {
    position: relative;
    width: 525px;
    height: 300px;
    border-radius: 4px;
    overflow: hidden;
    box-shadow: 0 10px 30px rgba(0,0,0,0.18);
  }

  /* Front */
  .card-front { background: var(--card-white); color: var(--ink-navy); }
  .brand {
    position: absolute;
    top: 30px;
    right: 34px;
    display: flex;
    flex-direction: column;
    align-items: center;
    gap: 14px;
  }
  .brand-mark {
    width: 96px;
    height: 96px;
    border-radius: 50%;
    background: var(--logo-plum);
  }
  .brand-name {
    font-weight: 700;
    font-size: 24px;
    letter-spacing: 1px;
    color: var(--ink-navy);
    white-space: nowrap;
  }
  .divider {
    position: absolute;
    left: 34px;
    right: 34px;
    top: 204px;
    height: 1px;
    background: var(--ink-navy);
  }
  .website {
    position: absolute;
    left: 34px;
    top: 226px;
    display: flex;
    align-items: center;
    gap: 10px;
    font-weight: 500;
    font-size: 16px;
    color: var(--ink-navy);
  }
  .website-icon {
    width: 14px;
    height: 14px;
    border-radius: 50%;
    background: var(--accent-red);
    flex: none;
  }

  /* Back */
  .card-back {
    background: linear-gradient(100deg, var(--flame-yellow) 0%, var(--flame-orange) 70%, var(--flame-deep) 100%);
  }
  .flame-art {
    position: absolute;
    left: 0;
    top: 0;
    width: 60%;
    height: 100%;
    background: radial-gradient(ellipse at 35% 70%, rgba(240,240,40,0.75), rgba(232,140,10,0.3) 60%, transparent 80%);
  }
  .back-brand {
    position: absolute;
    right: 34px;
    bottom: 58px;
    font-weight: 700;
    font-size: 26px;
    letter-spacing: 1px;
    color: var(--reverse-white);
    white-space: nowrap;
  }
</style>
</head>
<body>
  <section class="card card-front">
    <div class="brand">
      <div class="brand-mark"></div>
      <div class="brand-name">FERNCREST ROAM</div>
    </div>
    <div class="divider"></div>
    <div class="website"><span class="website-icon"></span>www.ferncrestroam.example</div>
  </section>

  <section class="card card-back">
    <div class="flame-art" role="img" aria-label="Large stylised flame illustration in yellow and orange"></div>
    <div class="back-brand">FERNCREST ROAM</div>
  </section>
</body>
</html>
```